App Design - Career Prep Pal

We require an App Design for our new App called 'Hiring Helper'. This app is essentially an assistant to help Users prepare for job interviews, to help them get hired. <br/><br/>Users who download the App can view common Questions and Answers, save their favourite responses and also view common Interview Tips. <br/><br/>The vision for our App is for Users who are preparing for an interview (1 week before, 1 day before, even 1 hour before), are able to download, view and educate themselves on common questions and responses, and then be confident to land the job. <br/><br/>Our team has developed wireframes to help highlight what each screen should do and include. Please see attached document, which also highlights key requirements for the experience. Feel free to add/remove/edit what you see on these wireframes. Our preference is that you use Adobe XD please.<br/><br/>In terms of design guidelines, we want the experience to be simple, intuitive and 'memorable' to help Users to remember the questions/responses when they are in the interview. <br/><br/>The final design should communicate 'neat and clean professionalism'; we like the design of: jobvista net au<br/><br/>Thank you for reading! Good luck !

Target Market(s)

Professional job seekers

Font styles to use
Sans Serif

Colors

Designer to choose colors to be used in the design.

Requirements
Must have
• Please see my PixelGuild_UX file that I have uploaded
Nice to have
• Could you also please include some ideas on how we can incorporate Advertising into the app screens

```html
<!DOCTYPE html>
<html lang="en">
<head>
<meta charset="utf-8">
<title>Hiring Helper – App Screens</title>
<link rel="stylesheet" href="https://fonts.googleapis.com/css2?family=Fira+Sans:wght@300;400;600;700&display=swap">
<style>
  :root {
    --canvas: #d6d6d6;
    --charcoal: #2b2b2b;
    --coral: #f26d55;
    --sky: #29c0e3;
    --paper: #f4f8fc;
    --band: #6f6f6f;
    --ink: #2b2b2b;
    --muted-light: #d8d8d8;
  }
  * { box-sizing: border-box; margin: 0; padding: 0; }
  html, body { width: 1200px; height: 810px; overflow: hidden; }
  body {
    background: var(--canvas);
    font-family: "Fira Sans", Arial, sans-serif;
    position: relative;
  }
  .screen {
    position: absolute;
    width: 281px;
    height: 608px;
    background: var(--paper);
    overflow: hidden;
  }
  .screen--splash { left: 124.5px; top: 75px; background: var(--charcoal); }
  .screen--home { left: 463.5px; top: 72px; }
  .screen--categories { left: 809px; top: 74px; }

  .wordmark {
    position: absolute;
    left: 0; right: 0;
    text-align: center;
    color: #ffffff;
    font-weight: 400;
    letter-spacing: 0.2px;
    white-space: nowrap;
  }
  .screen--splash .wordmark { top: 112px; font-size: 27px; }
  .screen--home .wordmark { top: 88px; font-size: 23px; }
  .screen--categories .wordmark { top: 52px; font-size: 17px; }

  /* Splash */
  .intro-frame { position: absolute; }
  .intro-frame .bar { position: absolute; }
  .bar--top { left: 24.5px; top: 189px; width: 216px; height: 7px; background: var(--coral); }
  .bar--left { left: 24.5px; top: 189px; width: 7px; height: 354px; background: var(--coral); }
  .bar--right { left: 250.5px; top: 215px; width: 7px; height: 356px; background: var(--sky); }
  .bar--bottom { left: 40.5px; top: 564px; width: 217px; height: 7px; background: var(--sky); }
  .intro-copy {
    position: absolute;
    left: 50px; top: 227px;
    width: 181px;
    text-align: center;
    color: var(--muted-light);
    font-weight: 300;
    font-size: 12.8px;
    line-height: 16.5px;
  }

  /* Headers */
  .app-header { position: absolute; left: 0; top: 0; width: 100%; background: var(--charcoal); }
  .screen--home .app-header { height: 142.5px; }
  .screen--categories .app-header { height: 87px; }
  .back-link {
    position: absolute; left: 14px; top: 17px;
    display: flex; align-items: center; gap: 6px;
    color: #ffffff; font-weight: 600; font-size: 12px; letter-spacing: 0.3px;
  }
  .section-band {
    position: absolute; left: 0; top: 87px; width: 100%; height: 35.5px;
    background: var(--band);
    color: #ffffff; font-weight: 700; font-size: 11.5px; letter-spacing: 0.4px;
    display: flex; align-items: center; justify-content: center;
  }
  .section-label {
    position: absolute; left: 26px; top: 153px;
    color: var(--ink); font-weight: 600; font-size: 11.6px; letter-spacing: 0.3px;
  }

  /* Menu tiles */
  .tile {
    position: absolute; left: 27px;
    width: 227px; height: 62px;
    border: 2.3px solid var(--sky);
    display: flex; align-items: center;
    color: var(--sky); font-weight: 600; font-size: 13px;
    line-height: 19.5px; letter-spacing: 0.4px;
    text-transform: uppercase;
  }
  .tile svg { position: absolute; left: 16px; top: 50%; transform: translateY(-50%); }
  .tile span { position: absolute; left: 66px; }
  .screen--categories .tile span { left: 65px; }
  .screen--categories .tile svg { left: 18px; }

  .tile--responses { top: 234px; }
  .tile--portfolio { top: 322px; }
  .tile--tips { top: 412px; }
  .tile--behavioral { top: 182px; }
  .tile--situational { top: 270px; }
  .tile--motivational { top: 360px; }
  .tile--technical { top: 449px; }

  .view-all {
    position: absolute; left: 91px; top: 539px;
    width: 100px; height: 35px;
    background: var(--coral); color: #ffffff;
    font-weight: 600; font-size: 13px; letter-spacing: 0.4px;
    display: flex; align-items: center; justify-content: center;
  }
</style>
</head>
<body>

  <!-- Splash screen -->
  <section class="screen screen--splash">
    <div class="wordmark">Hiring Helper</div>
    <div class="intro-frame">
      <div class="bar bar--top"></div>
      <div class="bar bar--left"></div>
      <div class="bar bar--right"></div>
      <div class="bar bar--bottom"></div>
    </div>
    <p class="intro-copy">Lorem Ipsum is simply dummy text of the printing and typese tting industry. Lorem Ipsum has been the industry's tand ard dummy text ever since the 1500s, when an unknown print er took a galley of type and scrambled it to make a type specimen book. It has survived not only five cen turies, but also the leap into electronic type setting, remaining essentially uncha nged. It was popularised in the 1960s with the Lorem Ipsum as their default model text, and a search.</p>
  </section>

  <!-- Home menu -->
  <section class="screen screen--home">
    <header class="app-header">
      <div class="wordmark">Hiring Helper</div>
    </header>

    <div class="tile tile--responses">
      <svg width="32" height="28" viewBox="0 0 32 28" aria-hidden="true">
        <path d="M2 4h17v12H9l-5 5v-5H2z" fill="var(--coral)"/>
        <path d="M12 9h18v13h-3v5l-5-5h-10z" fill="none" stroke="var(--coral)" stroke-width="1.6"/>
      </svg>
      <span>View Questions &amp;<br>Responses</span>
    </div>

    <div class="tile tile--portfolio">
      <svg width="32" height="30" viewBox="0 0 32 30" aria-hidden="true" fill="none" stroke="var(--coral)" stroke-width="1.6">
        <rect x="1" y="7" width="30" height="21"/>
        <path d="M11 7V2h10v5M1 15h30M14 13h4v5h-4z"/>
      </svg>
      <span>My Question<br>Portfolio</span>
    </div>

    <div class="tile tile--tips">
      <svg width="34" height="34" viewBox="0 0 34 34" aria-hidden="true" fill="none" stroke="var(--coral)" stroke-width="1.6">
        <path d="M17 7a7 7 0 0 0-4 12.7V24h8v-4.3A7 7 0 0 0 17 7z"/>
        <path d="M14 27h6M15 30h4M17 1v3M5 5l2 2M29 5l-2 2M1 16h3M30 16h3M5 27l2-2M29 27l-2-2"/>
      </svg>
      <span>Interview Tips</span>
    </div>
  </section>

  <!-- Category selection -->
  <section class="screen screen--categories">
    <header class="app-header">
      <div class="back-link">
        <svg width="8" height="13" viewBox="0 0 8 13" aria-hidden="true"><path d="M7 1L1.5 6.5 7 12" fill="none" stroke="#fff" stroke-width="1.8"/></svg>
        BACK
      </div>
      <div class="wordmark">Hiring Helper</div>
    </header>
    <div class="section-band">VIEW QUESTIONS &nbsp;&amp; RESPONSES</div>
    <div class="section-label">SELECT YOUR QUESTIONS CATEGORY</div>

    <div class="tile tile--behavioral">
      <svg width="30" height="32" viewBox="0 0 30 32" aria-hidden="true" fill="none" stroke="var(--coral)" stroke-width="1.4">
        <path d="M8 30v-5H5l-2-5 1-3a12 12 0 1 1 19 9v4"/>
        <circle cx="16" cy="12" r="6.5"/>
        <path d="M16 6v13M12 9c2 1 2 3 0 4M20 9c-2 1-2 3 0 4"/>
      </svg>
      <span>Behavioral</span>
    </div>

    <div class="tile tile--situational">
      <svg width="36" height="28" viewBox="0 0 36 28" aria-hidden="true" fill="none" stroke="var(--coral)" stroke-width="1.4">
        <path d="M2 10h6l12-7v20L8 16H2z"/>
        <path d="M6 16l2 10h4l-2-10M24 9c2 2 2 6 0 8M28 6c4 4 4 10 0 14"/>
      </svg>
      <span>Situational</span>
    </div>

    <div class="tile tile--motivational">
      <svg width="26" height="36" viewBox="0 0 26 36" aria-hidden="true" fill="none" stroke="var(--coral)" stroke-width="1.4">
        <path d="M13 2a11 11 0 0 0-6 20v4h12v-4A11 11 0 0 0 13 2z"/>
        <path d="M13 4v18M8 9c3 1 3 4 0 5M18 9c-3 1-3 4 0 5"/>
        <path d="M8 29h10M9 32h8M11 35h4"/>
      </svg>
      <span>Motivational</span>
    </div>

    <div class="tile tile--technical">
      <svg width="30" height="28" viewBox="0 0 30 28" aria-hidden="true" fill="none" stroke="var(--coral)" stroke-width="1.6">
        <path d="M3 20v-6a12 12 0 0 1 24 0v6"/>
        <rect x="2" y="18" width="5" height="8" rx="1.5"/>
        <rect x="23" y="18" width="5" height="8" rx="1.5"/>
      </svg>
      <span>Technical</span>
    </div>

    <div class="view-all">VIEW ALL</div>
  </section>

</body>
</html>
```